Business Card Design for Software Development Company

I am looking for a business card design the incorporates my new logo (attached below).

Key information to include:
Name: Martin Quelbrook
Title: CEO
Email: martin@brightwellcivic.example
Phone: 555-218-9403
Website: www.brightwellcivic.example

NOTE: This design should be easy to edit so that we can order cards for different members of our team.

```html
<!DOCTYPE html>
<html lang="en">
<head>
<meta charset="utf-8">
<title>Brightwell Labs – Business Card</title>
<link rel="stylesheet" href="https://fonts.googleapis.com/css2?family=Montserrat:wght@300;400;700;800&display=swap">
<style>
  :root {
    --backdrop: #3a3a3a;
    --card: #222222;
    --edge: #1fa89a;
    --teal: #1fa89a;
    --orange: #ee7d22;
    --white: #ffffff;
    --soft-white: #e9e9e9;
    --glow-teal: rgba(31, 120, 110, 0.35);
    --glow-brown: rgba(120, 70, 40, 0.35);
  }
  * { box-sizing: border-box; margin: 0; padding: 0; }
  html, body { width: 1200px; height: 900px; overflow: hidden; }
  body {
    background: var(--backdrop);
    font-family: "Montserrat", Arial, sans-serif;
    position: relative;
  }
  .card {
    position: absolute;
    left: 250px;
    width: 700px;
    height: 400px;
    background: var(--card);
    border-bottom: 6px solid var(--edge);
    overflow: hidden;
  }
  .card--front { top: 30px; }
  .card--back  { top: 465px; }

  .front-glow {
    position: absolute;
    inset: 0;
    background:
      radial-gradient(ellipse 320px 200px at 30% 25%, var(--glow-teal), transparent 70%),
      radial-gradient(ellipse 260px 260px at 48% 55%, var(--glow-brown), transparent 70%);
  }

  .wordmark {
    position: absolute;
    display: flex;
    align-items: center;
    gap: 18px;
    color: var(--white);
    font-weight: 700;
    letter-spacing: -0.5px;
    white-space: nowrap;
  }
  .wordmark__square {
    background: var(--orange);
    flex: none;
  }
  .card--front .wordmark { left: 110px; top: 165px; font-size: 60px; }
  .card--front .wordmark__square { width: 38px; height: 38px; }
  .card--back .wordmark { left: 150px; top: 60px; font-size: 54px; }
  .card--back .wordmark__square { width: 34px; height: 34px; }

  .person {
    position: absolute;
    right: 362px;
    top: 258px;
    text-align: right;
  }
  .person__name {
    font-weight: 800;
    font-size: 30px;
    letter-spacing: 0.5px;
    white-space: nowrap;
  }
  .person__first { color: var(--teal); }
  .person__last { color: var(--orange); }
  .person__title {
    color: var(--soft-white);
    font-weight: 300;
    font-size: 19px;
    letter-spacing: 1px;
    margin-top: 2px;
  }

  .divider {
    position: absolute;
    left: 356px;
    top: 228px;
    width: 1.5px;
    height: 92px;
    background: var(--teal);
  }

  .contact {
    position: absolute;
    left: 378px;
    top: 226px;
    list-style: none;
  }
  .contact__item {
    display: flex;
    align-items: center;
    gap: 10px;
    color: var(--soft-white);
    font-weight: 400;
    font-size: 15px;
    line-height: 32px;
    white-space: nowrap;
  }
  .contact__icon { width: 14px; height: 14px; flex: none; }
</style>
</head>
<body>

<section class="card card--front" aria-label="Card front">
  <div class="front-glow"></div>
  <div class="wordmark">
    <span class="wordmark__square"></span>
    <span class="wordmark__name">BrightwellLabs</span>
  </div>
</section>

<section class="card card--back" aria-label="Card back">
  <div class="wordmark">
    <span class="wordmark__square"></span>
    <span class="wordmark__name">BrightwellLabs</span>
  </div>

  <div class="person">
    <p class="person__name"><span class="person__first">Martin</span> <span class="person__last">Quelbrook</span></p>
    <p class="person__title">CEO</p>
  </div>

  <div class="divider"></div>

  <ul class="contact">
    <li class="contact__item">
      <svg class="contact__icon" viewBox="0 0 16 16" aria-hidden="true">
        <path fill="#ee7d22" d="M3.2 1.5l2.4 0 1.1 3.2-1.6 1.1c.8 1.8 2.2 3.2 4 4l1.1-1.6 3.2 1.1v2.4c0 .9-.7 1.6-1.6 1.6C6.5 13.3 2.7 9.5 1.6 3.1 1.6 2.2 2.3 1.5 3.2 1.5z"/>
      </svg>
      <span>555-218-9403</span>
    </li>
    <li class="contact__item">
      <svg class="contact__icon" viewBox="0 0 16 16" aria-hidden="true">
        <rect x="1" y="3" width="14" height="10" rx="1" fill="#ee7d22"/>
        <path d="M1.5 3.8L8 9l6.5-5.2" fill="none" stroke="#222222" stroke-width="1.3"/>
      </svg>
      <span>martin@brightwellcivic.example</span>
    </li>
    <li class="contact__item">
      <svg class="contact__icon" viewBox="0 0 16 16" aria-hidden="true">
        <circle cx="8" cy="8" r="6.5" fill="none" stroke="#ee7d22" stroke-width="1.4"/>
        <ellipse cx="8" cy="8" rx="2.8" ry="6.5" fill="none" stroke="#ee7d22" stroke-width="1.2"/>
        <path d="M1.5 8h13" stroke="#ee7d22" stroke-width="1.2"/>
      </svg>
      <span>www.brightwellcivic.example</span>
    </li>
  </ul>
</section>

</body>
</html>
```